Flyer für ambulanten Pflegedienst
Zielgruppe
Ambulanter Pflegedienst, Potentielle Kunden für Grund- und Behandlungspflege, nicht nur Pflegebedürftige, sondern auch Angehörige. Flyer dient zur Auslage, beispielsweise in Wartezimmern von Ärzten.
Aufgabenstellung
Ausführliches Briefing mit Aufbau und Text in der Anlage, ebenso das Bildmaterial, Fonts, Logos. Flyer in A4 Wickelfalz, bitte die Gestaltungsvorlage mit den Maßen des Druckanbieters (ebenfalls anbei) beachten. Vorerst hauptsächlich KI-generierte/Stockfotos vorhanden, Fotoshooting folgt im Juli und Bilder werden dann ggf. nochmal ersetzt um persönliche Ebene zu erzeugen. Der erste Wurf muss aber vorerst so erfolgen. Übergabe der Daten: Druckfähiges PDF, PDF mit Ebenen und AI

```html
<!DOCTYPE html>
<html lang="de">
<head>
<meta charset="utf-8">
<title>Hollwede Hauskrankenpflege – Flyer Wickelfalz</title>
<link href="https://fonts.googleapis.com/css2?family=Nunito:wght@700;800&family=Inter:wght@400;600;700&display=swap" rel="stylesheet">
<style>
:root{
  --navy:#13267e;
  --navy-deep:#0c1c66;
  --blue:#2c4aa8;
  --sky:#3aa6e0;
  --green:#1d7a3a;
  --green-deep:#155f2c;
  --paper:#f4f5f7;
  --card:#e9ebef;
  --ink:#1f2430;
  --muted:#5a6070;
  --stage:#e3e3e3;
}
*{box-sizing:border-box;margin:0;padding:0}
html,body{width:1200px;height:1200px;overflow:hidden}
body{background:var(--stage);font-family:"Inter",sans-serif;color:var(--ink);position:relative}
.spread{position:absolute;left:225px;width:750px;height:540px;display:flex;box-shadow:0 6px 18px rgba(0,0,0,.12)}
.spread--outside{top:40px}
.spread--inside{top:620px}
.panel{width:250px;height:540px;position:relative;overflow:hidden}
.eyebrow{font-size:6.5px;letter-spacing:.12em;font-weight:600;text-transform:uppercase;color:var(--sky)}
.headline{font-family:"Nunito",sans-serif;font-weight:800;line-height:1.08}
.body{font-size:7.3px;line-height:1.5}
.photo{position:absolute}
.brand{font-family:"Inter",sans-serif;font-weight:600;display:flex;align-items:center;gap:4px}
.brand .dot{width:8px;height:8px;border-radius:50%;background:currentColor;flex:none}

/* panel 1 */
.p-about{background:linear-gradient(180deg,#f6f7f9 0%,#f1f2f5 55%,#2c47a6 72%,var(--navy-deep) 100%)}
.p-about .top{padding:26px 20px 0}
.p-about .headline{font-size:17px;color:var(--navy);margin:6px 0 12px;max-width:200px}
.p-about .body p{margin-bottom:6px}
.p-about .photo{left:0;top:210px;width:235px;height:182px;border-radius:0 50% 50% 0/0 50% 50% 0;background:linear-gradient(160deg,#c8b8a8 0%,#7e88bd 45%,#3350ac 78%,#2a45a4 100%)}
.p-about .contact{position:absolute;left:20px;right:16px;top:372px;color:#fff}
.p-about .contact h3{font-family:"Nunito",sans-serif;font-weight:700;font-size:11.5px;color:#5fc2f0;margin-bottom:5px}
.p-about .contact .body{font-size:6.8px;color:#dde3f5}
.p-about .row{display:flex;justify-content:space-between;align-items:center;margin-top:14px}
.p-about .brand{color:#fff;font-size:9.5px}
.info{font-size:6px;line-height:1.9;color:#dde3f5}
.info b{color:#fff}
.info .ic{display:inline-block;width:5px;height:5px;border-radius:50%;background:var(--sky);margin-right:3px;vertical-align:middle}
.p-about .foot{display:flex;justify-content:space-between;margin-top:12px;border-top:1px solid rgba(255,255,255,.25);padding-top:8px;font-size:6px;line-height:1.5;color:#dde3f5}
.p-about .foot b{color:#fff;display:block}
.label{color:var(--sky);display:block}

/* panel 2 */
.p-house{background:var(--paper)}
.p-house .photo{left:0;top:0;width:250px;height:128px;background:linear-gradient(180deg,#9fb8a6,#cfd8d0 70%,var(--paper))}
.p-house .brand{position:absolute;top:22px;left:20px;color:var(--green);font-size:9.5px}
.p-house .content{position:absolute;top:128px;left:0;right:0;padding:0 20px}
.p-house .eyebrow{color:#3b4250}
.p-house .headline{font-size:16.5px;color:var(--green);margin:5px 0 9px}
.svc{display:flex;gap:9px;margin-top:9px}
.svc .ic{width:19px;height:19px;border-radius:50%;border:1.5px solid var(--green);flex:none;margin-top:2px}
.svc h4{font-size:7px;color:var(--green);font-weight:700}
.svc p{font-size:6.8px;line-height:1.45}
.p-house .reach{position:absolute;left:0;right:0;bottom:0;height:152px;background:linear-gradient(180deg,var(--green),var(--green-deep));color:#fff;padding:14px 20px}
.p-house .reach h3{font-family:"Nunito",sans-serif;font-weight:700;font-size:11.5px;color:#7fd49a;margin-bottom:4px}
.p-house .reach .body{font-size:6.8px;color:#e0f0e4}
.p-house .cols{display:flex;justify-content:space-between;margin-top:12px}
.p-house .info{color:#e0f0e4}
.p-house .info .ic{background:#7fd49a}
.p-house .side{border-left:1px solid rgba(255,255,255,.3);padding-left:10px;font-size:6px;line-height:1.5}
.p-house .side .brand{position:static;color:#fff;font-size:8px;margin-bottom:12px}
.p-house .side .label{color:#7fd49a}

/* panel 3 cover */
.p-cover{background:linear-gradient(180deg,#c9c2b8 0%,#8f93ad 35%,#3d55ac 62%,var(--blue) 100%)}
.p-cover .photo{inset:0 0 200px 0;background:linear-gradient(160deg,#d9d2c6,#8e97c0 55%,rgba(61,85,172,0))}
.p-cover .brand{position:absolute;top:30px;left:0;right:0;justify-content:center;color:var(--navy);font-size:12px}
.p-cover .text{position:absolute;left:22px;right:20px;top:312px;color:#fff}
.p-cover .headline{font-size:20px}
.p-cover .sub{font-family:"Nunito",sans-serif;font-weight:700;font-size:11px;color:#5fc2f0;margin-top:9px;line-height:1.35}
.p-cover hr{width:14px;border:0;border-top:1.2px solid #fff;margin:12px 0}
.p-cover .body{font-size:6.8px;color:#e3e8f7}
.stats{display:flex;margin-top:14px;font-size:6.5px;font-weight:700;line-height:1.3}
.stats div{flex:1;text-align:center;border-left:1px solid rgba(255,255,255,.45)}
.stats div:first-child{border:0;text-align:left}

/* panel 4 */
.p-who{background:linear-gradient(180deg,var(--navy) 0%,#2a49a8 55%,#16307f 100%)}
.p-who .content{padding:28px 24px 0;color:#dde3f5}
.p-who .eyebrow{color:#fff}
.p-who .headline{font-size:16.5px;color:#5fc2f0;margin:6px 0 12px}
.p-who .body p{margin-bottom:6px}
.p-who blockquote{border-left:1.5px solid var(--sky);padding-left:12px;margin-top:12px;font-family:"Nunito",sans-serif;font-weight:700;font-size:11px;line-height:1.3;color:#fff}
.p-who .photo{left:0;right:0;bottom:0;height:225px;background:linear-gradient(180deg,rgba(22,48,127,0),#6e7f72 35%,#3b4d8a 80%,#1e2f6e)}
.p-who .brand{position:absolute;left:6px;bottom:8px;color:#fff;font-size:9.5px}

/* panel 5 */
.p-services{background:var(--paper);padding:28px 20px 0}
.p-services .headline{font-size:16.5px;color:var(--navy);margin:6px 0 10px}
.card{background:var(--card);padding:11px 12px;height:88px;margin-bottom:10px}
.card .hd{display:flex;align-items:center;gap:10px;margin-bottom:10px}
.card .ic{width:22px;height:22px;border-radius:50%;border:1.8px solid var(--navy);position:relative;flex:none}
.card .ic::after{content:"";position:absolute;inset:5px;border-radius:2px;background:var(--sky)}
.card h4{font-family:"Nunito",sans-serif;font-weight:800;font-size:10px;color:var(--navy);line-height:1.15}
.card p{font-size:6.3px;line-height:1.55;color:var(--muted)}
.p-services .cards{margin-top:14px}

/* panel 6 */
.p-services2{background:var(--paper)}
.p-services2 .photo{left:0;top:10px;width:250px;height:212px;border-radius:50%/50%;background:linear-gradient(135deg,#d8cfc2,#8fb3c7 55%,#3a6fc2)}
.p-services2 .cards{position:absolute;left:20px;right:20px;top:238px}
</style>
</head>
<body>

<section class="spread spread--outside">
  <article class="panel p-about">
    <div class="top">
      <p class="eyebrow">Was uns besonders macht</p>
      <h2 class="headline">Pflege braucht Vertrau­en. Und Menschen, die da sind.</h2>
      <div class="body">
        <p>Gute Pflege entsteht durch Aufmerksamkeit, Erfahrung und ein verlässliches Team.</p>
        <p>Bei der Hauskrankenpflege Hollwede arbeiten engagierte Pflegekräfte, Betreuungskräfte und Fachpersonen Hand in Hand – mit Herz, Respekt und fachlicher Kompetenz. Über 40 Mitarbeitende geben Tag für Tag ihr Bestes für Sie und Ihre Angehörigen.</p>
      </div>
    </div>
    <div class="photo" role="img" aria-label="Foto: Pflegekraft legt einer älteren Dame im Sessel eine Decke um"></div>
    <div class="contact">
      <h3>Wir sind für Sie da.</h3>
      <p class="body">Sie möchten sich informieren oder ein persönliches Gespräch vereinbaren? Wir beraten Sie gerne – unkompliziert, persönlich und unverbindlich.</p>
      <div class="row">
        <div class="brand"><span class="dot"></span>Hollwede Pflege</div>
        <div class="info">
          <b><span class="ic"></span>05131 - 48 27 0</b><br>
          <span class="ic"></span>info@hollwede-pflege.de<br>
          <span class="ic"></span>www.hollwede-pflege.de
        </div>
      </div>
      <div class="foot">
        <div><b>Hauskrankenpflege Hollwede</b>Lindenweg 14 · 49682 Talbrück</div>
        <div><span class="label">Bürozeiten:</span>Mo., Di., Mi., Fr. 9 bis 12<br>Uhr und Do. 15 bis 17 Uhr</div>
      </div>
    </div>
  </article>

  <article class="panel p-house">
    <div class="photo" role="img" aria-label="Foto: lächelnde Hauswirtschaftskraft in grünem Shirt mit Reinigungsutensilien"></div>
    <div class="brand"><span class="dot"></span>Hollwede Hausdienste</div>
    <div class="content">
      <p class="eyebrow">Hauswirtschaftliche Versorgung</p>
      <h2 class="headline">Hilfe im Haushalt.<br>Entlastung im Alltag.</h2>
      <p class="body">Damit Sie sich zuhause weiterhin wohlfühlen können, bieten über 25 Kolleginnen im Team der Hollwede Hausdienste fachgerechte und zuverlässige Unterstützung in verschiedenen Bereichen:</p>
      <div class="svc"><span class="ic"></span><div><h4>Hilfe im Haushalt</h4><p>Unterstützung bei alltäglichen Aufgaben – von der Grundreinigung bis zur Wäschepflege.</p></div></div>
      <div class="svc"><span class="ic"></span><div><h4>Alltagsbegleitung</h4><p>Niemand ist gern allein und wir sind für Sie da, wenn Sie Gesellschaft wünschen.</p></div></div>
      <div class="svc"><span class="ic"></span><div><h4>Betreuung</h4><p>Strukturierte Betreuung und Hilfe nach individuellem Bedarf.</p></div></div>
    </div>
    <div class="reach">
      <h3>So erreichen Sie uns</h3>
      <p class="body">Das Team der Hollwede Hausdienste steht Ihnen bei Fragen und Terminwünschen gern zur Verfügung:</p>
      <div class="cols">
        <div class="info">
          <b>Hollwede Hausdienste GmbH</b><br>Lindenweg 14 · 49682 Talbrück<br>
          <b><span class="ic"></span>05131 - 77 31 406</b><br>
          <span class="ic"></span>info@hollwede-hausdienste.de<br>
          <span class="ic"></span>www.hollwede-hausdienste.de
        </div>
        <div class="side">
          <div class="brand"><span class="dot"></span>Hausdienste</div>
          <span class="label">Bürozeiten:</span>Mo., Di., Do., Fr.<br>8 bis 11 Uhr
        </div>
      </div>
    </div>
  </article>

  <article class="panel p-cover">
    <div class="photo" role="img" aria-label="Foto: Pflegerin in blauem Poloshirt im Gespräch mit einer älteren Frau im Wohnzimmer"></div>
    <div class="brand"><span class="dot"></span>Hollwede Pflege</div>
    <div class="text">
      <h1 class="headline">Weil das eigene Zuhause Lebensqualität ist.</h1>
      <p class="sub">Ihr ambulanter Pflegedienst<br>für die Region.</p>
      <hr>
      <p class="body">Seit über 30 Jahren begleiten wir Menschen im Raum Talbrück und Wiesenau in ihrem vertrauten Zuhause – individuell, menschlich und mit fachlicher Kompetenz.</p>
      <div class="stats"><div>24h<br>erreichbar</div><div>Persönliche<br>Beratung</div><div>MD-geprüfte<br>Qualität</div></div>
    </div>
  </article>
</section>

<section class="spread spread--inside">
  <article class="panel p-who">
    <div class="content">
      <p class="eyebrow">Wer wir sind</p>
      <h2 class="headline">Vertrauen beginnt mit Zuhören.</h2>
      <div class="body">
        <p>Pflege bedeutet für uns mehr als Versorgung. Es geht um Menschen, ihre Gewohnheiten, ihre Wünsche und das gute Gefühl, in den eigenen vier Wänden bleiben zu können.</p>
        <p>Deshalb nehmen wir uns Zeit für persönliche Gespräche und individuelle Lösungen. Gemeinsam mit unseren Kundinnen, Kunden und Angehörigen gestalten wir eine Unterstützung, die zum Leben passt – nicht umgekehrt.</p>
        <p>Als ambulanter Pflegedienst begleiten wir Menschen im Raum Talbrück und Wiesenau zuverlässig im Alltag und stehen auch Angehörigen beratend zur Seite.</p>
      </div>
      <blockquote>„Unsere Pflege orientiert sich am Befinden der Menschen – nicht am Befund.“</blockquote>
    </div>
    <div class="photo" role="img" aria-label="Foto: zwei Pflegekräfte begleiten eine ältere Dame vom Dienstwagen"></div>
    <div class="brand"><span class="dot"></span>Hollwede Pflege</div>
  </article>

  <article class="panel p-services">
    <p class="eyebrow">Unsere Leistungen</p>
    <h2 class="headline">Unterstützung, die den Alltag leichter macht.</h2>
    <p class="body">Jeder Mensch braucht etwas anderes. Deshalb richten wir unsere Leistungen individuell nach Ihrer persönlichen Situation aus.</p>
    <div class="cards">
      <div class="card"><div class="hd"><span class="ic"></span><h4>Grundpflege</h4></div><p>Unterstützung bei Körperpflege, Mobilität, Ernährung und allem, was Sicherheit im Alltag gibt.</p></div>
      <div class="card"><div class="hd"><span class="ic"></span><h4>Behandlungspflege</h4></div><p>Medizinische Versorgung nach ärztlicher Verordnung – zum Beispiel Wundversorgung, Medikamentengabe oder Injektionen.</p></div>
      <div class="card"><div class="hd"><span class="ic"></span><h4>Betreuung<br>&amp; Alltagsbegleitung</h4></div><p>Begleitung im Alltag, stundenweise Betreuung, Unterstützung bei Demenz sowie Entlastung für Angehörige.</p></div>
      <div class="card"><div class="hd"><span class="ic"></span><h4>Verhinderungspflege</h4></div><p>Auszeiten im Rahmen der Verhinderungspflege, denn auch pflegende Angehörige müssen mal durchatmen.</p></div>
    </div>
  </article>

  <article class="panel p-services2">
    <div class="photo" role="img" aria-label="Foto: Pflegerin und lächelnde Seniorin sitzen sich im Wohnzimmer gegenüber, daneben ein Rollator"></div>
    <div class="cards">
      <div class="card"><div class="hd"><span class="ic"></span><h4>Beratung</h4></div><p>Pflegeberatung nach § 37.3 SGB XI zur Sicherstellung des Pflegegeld-Bezugs, Unterstützung bei Anträgen und Hilfe bei allen Fragen rund um Pflegeleistungen.</p></div>
      <div class="card"><div class="hd"><span class="ic"></span><h4>Hausnotruf<br>&amp; Erreichbarkeit</h4></div><p>Sicherheit rund um die Uhr – mit einem Team, das erreichbar bleibt.</p></div>
      <div class="card"><div class="hd"><span class="ic"></span><h4>Palliative Versorgung</h4></div><p>Als spezialisierter Anbieter ist uns die Versorgung und Begleitung zum Ende des Lebens ein besonderes Herzensanliegen.</p></div>
    </div>
  </article>
</section>

</body>
</html>
```